Bold, Modern, Clean "Kestrelwaymassage.com" website

Why we stand out?
We are a male and female mobile massage team. Our names are Paul and Lina. 
Kestrel Way is a Seattle based mobile massage service. Our massage is offered to the community with a goal of facilitating balance within each individual. We specialize in integrated Pain management, and sports/medical massage therapy. Every client's first assessment is attended by our male and female massage therapist team. Depending on the goals identified for an individual determines which therapist will be assigned to provide treatment, if not both.

Our passion...
Here at Kestrel Way, we have a great passion for Postural Resoration and how it is integrated into an individual's Massage treatment. We pride ourselves in being natural facilitators of healing, which takes the ego of the therapist out of the client's healing process. We strive to deliver the best massage possible by including modalities such as Neuromuscular, Myofascial release, spontaneous muscle release, postural restoration, orthopedic, and medical massage.

Our education...

We are both Graduates of Venmora, school of massage therapy. We have continuing education in medical massage, myofacial release, trigger point therapy, postural restoration, anatomy, and spontaneous muscle release. Lina is also a Certified Yoga Instructor, which amplifies her experience with flexibility and strength as it pertains to each individual. Paul's passion is Massage, stretching, and strength training to encourage postural restoration and realignment.

Our rates-

Our rates are $75/ 60 minutes, $95/ 90 minutes, and $120/ 120 minutes.

Education-
Both Lina and I worked as behavioral health professionals that specialized in life skills mentoring for youth who had experienced different types of trauma. This led us both to want to help others in a different environment, where individuals can be empowered to take responsibility over their own healing. To us, massage is a type of manipulation physical therapy, that encourages healing on many levels.

Advice to any massage client-
The most important thing to 'us', as Licenced providers is to get you on to our table to show you our skills. But a good therapist never forgets that it's not about what we do for you, but what we can facilitate for you. Your health and healing has nothing to do with us. It is yours, not ours. Identify what your goals are with any Therapist, and know what the end looks like. Progress should be tangible, such as range of motion, and decreased pain.

Lina and Paul at Kestrel Way are awesome! I recently had open heart surgery, and Lina worked on me to increase my range of motion while helping with the pinched nerve from my arm being in the same position for so long during my surgery. My wife drives a lot for work, and Paul has helped decrease her neck and lower back pain immensely. They are seriously the best therapists I have ever worked with. I would recommend them to anyone who needs anything from stress relief to a medical massage treatment. They are professional, up beat, easy going, and always on time. And, I love that they meet us where ever we like! We did a staycation recently, where they came to our hotel to give us relaxation massages. Although usually they come to our home, where we focus on pain related issues. We will continue to work with them for a long, long time.

Target Market(s)

Mobile massage therapy clients

Industry/Entity Type

Massage Therapy

Coding

Coded - Design and coding required

Number of Pages Required

1 page

Font styles to use
Serif
Sans Serif

Requirements
Must have
• Please add or remove any information that would help the presentation of our website. Our logo is posted below, please include into the website.
• Please include a contact field that includes, kestrelwaymassage@fernmail.net,
• (206) 555-0148
• We have also included our own stock photos, as well as a photo of Paul and Lina. Please include a cropped photo of both massage therapists.

```html
<!DOCTYPE html>
<html lang="en">
<head>
<meta charset="utf-8">
<title>Kestrel Way Mobile Massage</title>
<link href="https://fonts.googleapis.com/css2?family=Merriweather:wght@400;700&family=Open+Sans:wght@400;600;700&display=swap" rel="stylesheet">
<style>
:root{
  --navy:#1f1f5c;
  --navy-deep:#1b1c4a;
  --band:#23264f;
  --teal:#13a6c9;
  --teal-dark:#0d7f9c;
  --ink:#222;
  --muted:#888;
  --card:#ededed;
  --chip:#3a3a3a;
  --footer:#1b1b1b;
  --star:#f6b21a;
  --white:#fff;
}
*{margin:0;padding:0;box-sizing:border-box}
html,body{width:1200px;height:2804px;overflow:hidden}
body{font-family:"Open Sans",Arial,sans-serif;color:var(--ink);background:var(--white);position:relative}
.abs{position:absolute}
h2{font-family:"Merriweather",Georgia,serif;font-weight:700;font-size:28px;color:var(--navy);text-align:center}
.rule{width:90px;height:2px;background:#ccc;margin:12px auto 0;position:relative}
.rule::after{content:"";position:absolute;left:30px;width:30px;top:0;height:2px;background:var(--navy)}
.band .rule{background:rgba(255,255,255,.35)}
.band .rule::after{background:#fff}

/* top bar */
.topbar{top:0;left:0;width:1200px;height:30px;background:var(--navy)}
.topbar .phone{position:absolute;right:120px;top:6px;color:#fff;font-size:13px;display:flex;gap:8px;align-items:center}
.navbar{top:30px;left:0;width:1200px;height:86px;background:#fff}
.logo{top:8px;left:100px;width:136px;height:136px;border-radius:50%;background:#fff;z-index:5;display:flex;align-items:center;justify-content:center;box-shadow:0 2px 6px rgba(0,0,0,.15)}
.logo-mark{width:118px;height:118px;border-radius:50%;background:var(--navy);display:flex;align-items:center;justify-content:center;text-align:center;color:#fff;font-family:"Merriweather",Georgia,serif;font-weight:700;font-size:17px;line-height:1.15}
.nav{position:absolute;top:30px;left:420px;display:flex;gap:37px;font-size:14px;color:#555}
.nav .active{color:var(--navy);font-weight:600;border-bottom:2px solid var(--navy);padding-bottom:8px}

/* hero */
.hero{top:116px;left:0;width:1200px;height:514px;background:linear-gradient(100deg,#d9a98c 0%,#b98066 30%,#7d4d3a 55%,#c9a48a 80%,#e8d3c2 100%)}
.form{top:105px;left:101px;width:257px;height:317px;background:rgba(40,40,110,.88);padding:45px 26px 0}
.form .field{height:46px;border:1px solid rgba(255,255,255,.45);color:#fff;font-size:12px;padding:14px 14px;margin-bottom:21px}
.form .btn{height:44px;background:var(--teal);color:#fff;font-size:13px;font-weight:700;text-align:center;line-height:44px}
.hero h1{position:absolute;left:380px;top:160px;font-family:"Merriweather",Georgia,serif;color:#fff;font-size:38px;line-height:1.4;text-align:left;text-shadow:0 2px 6px rgba(0,0,0,.5)}
.hero .arrow{position:absolute;top:240px}

/* what we do */
.services{top:640px;left:0;width:1200px}
.service{position:absolute;top:100px;width:300px;text-align:center}
.service .icon{width:140px;height:140px;border-radius:50%;margin:0 auto;background:#8d8fd9;border:4px solid var(--navy);box-shadow:0 0 0 3px #dedff4}
.service h3{font-family:"Merriweather",Georgia,serif;font-weight:400;color:var(--navy);font-size:20px;margin-top:20px}
.service p{font-size:12px;color:var(--muted);line-height:1.75;margin-top:8px}

/* rating band */
.band{background:var(--band);color:#fff}
.rating{top:1043px;left:0;width:1200px;height:343px;background:linear-gradient(90deg,#1e2148,#2a2e5c 60%,#1e2148)}
.rating h2,.clients h2{color:#fff}
.stars{position:absolute;top:105px;left:0;width:1200px;display:flex;justify-content:center;gap:10px}
.rating p{position:absolute;top:158px;left:270px;width:660px;font-size:13px;line-height:1.85;text-align:center}
.btn-book{position:absolute;top:255px;left:490px;width:220px;height:46px;background:var(--teal);color:#fff;font-weight:700;font-size:14px;text-align:center;line-height:46px}

/* rates */
.rates{top:1400px;left:0;width:1200px}
.card{position:absolute;top:130px;width:223px;height:299px;background:var(--card);text-align:center}
.card .price{position:absolute;top:-43px;left:66px;width:90px;height:90px;border-radius:50%;background:var(--chip);color:#fff;border:4px solid #fff;padding-top:18px}
.card .price b{font-weight:400;font-size:24px;display:block;line-height:1}
.card .price span{font-size:12px}
.card h4{margin-top:63px;font-size:16px;font-weight:600}
.card ul{list-style:none;margin:18px 28px 0;font-size:13px;color:#777}
.card li{padding:12px 0;border-bottom:1px solid #ddd}
.card li:last-child{border-bottom:0}
.card .book{width:136px;height:34px;line-height:34px;margin:14px auto 0;background:var(--chip);color:#fff;font-size:13px}
.card.featured{background:var(--teal);color:#fff}
.card.featured .price{background:var(--teal)}
.card.featured ul{color:#fff}
.card.featured li{border-color:rgba(255,255,255,.3)}
.card.featured .book{background:var(--teal-dark)}

/* clients */
.clients{top:1900px;left:0;width:1200px;height:396px;background:linear-gradient(90deg,#1c1d45,#2c2b55 50%,#1d1e46)}
.client{position:absolute;top:136px;display:flex;align-items:center;gap:22px}
.client .photo{width:120px;height:120px;border-radius:50%;background:linear-gradient(135deg,#caa792,#7a5a4a);border:4px solid #fff}
.client.active .photo{border-color:var(--teal)}
.client .name{font-family:"Merriweather",Georgia,serif;font-size:13px;font-weight:700}
.client .role{font-size:11px;color:#aaa;margin-top:4px}
.clients blockquote{position:absolute;top:276px;left:330px;width:540px;text-align:center;font-size:13px;line-height:1.85}
.clients .arrow{position:absolute;top:180px}

/* passion */
.passion{top:2296px;left:0;width:1200px;height:397px}
.passion .lead{position:absolute;top:78px;left:190px;width:820px;text-align:center;font-size:13px;color:#777;line-height:1.85}
.pitem{position:absolute;width:330px}
.pitem h5{font-family:"Merriweather",Georgia,serif;font-size:17px;font-weight:700;color:#111}
.pitem p{font-size:12px;color:#888;line-height:1.8;margin-top:6px}
.pitem.left{text-align:right}
.picon{position:absolute;width:80px;height:80px;border-radius:50%;background:var(--navy);border:4px solid #fff;box-shadow:0 0 0 2px #cfd0e6}
.center-logo{position:absolute;top:170px;left:530px;width:140px;height:140px;border-radius:50%;background:var(--navy);border:5px solid #fff;box-shadow:0 0 0 2px #cfd0e6;display:flex;align-items:center;justify-content:center;text-align:center;color:#fff;font-family:"Merriweather",Georgia,serif;font-weight:700;font-size:19px;line-height:1.15}

/* footer */
.footer{top:2693px;left:0;width:1200px;height:111px;background:var(--footer);color:#ddd;font-size:13px}
.footer nav{position:absolute;top:32px;left:0;width:1200px;text-align:center;word-spacing:6px}
.footer .copy{position:absolute;top:68px;left:0;width:1200px;text-align:center}
.social{position:absolute;top:38px;left:954px;display:flex;gap:9px}
.social span{width:26px;height:26px;border:2px solid #ddd;border-radius:50%}
</style>
</head>
<body>

<div class="abs topbar"><div class="phone">
<svg width="12" height="12" viewBox="0 0 24 24"><path fill="#fff" d="M6.6 10.8c1.4 2.8 3.8 5.1 6.6 6.6l2.2-2.2c.3-.3.7-.4 1-.2 1.1.4 2.3.6 3.6.6.6 0 1 .4 1 1V20c0 .6-.4 1-1 1C10.6 21 3 13.4 3 4c0-.6.4-1 1-1h3.5c.6 0 1 .4 1 1 0 1.3.2 2.5.6 3.6.1.3 0 .7-.2 1z"/></svg>
Call Now : (206) 555-0148</div></div>

<header class="abs navbar">
  <nav class="nav"><span class="active">Home</span><span>About Us</span><span>Services</span><span>Our Passion</span><span>Testimonials</span><span>Pricing</span><span>Contacts</span>
  <svg width="14" height="14" viewBox="0 0 24 24" style="margin-top:3px"><circle cx="10" cy="10" r="6" fill="none" stroke="#333" stroke-width="3"/><path d="M15 15l6 6" stroke="#333" stroke-width="3"/></svg></nav>
</header>
<div class="abs logo"><div class="logo-mark">KESTREL<br>WAY</div></div>

<section class="abs hero" role="img" aria-label="Woman relaxing during a back massage with flower petals">
  <div class="abs form">
    <div class="field">Enter Your Name</div>
    <div class="field">Address</div>
    <div class="field">Phone</div>
    <div class="btn">SUBSCRIBE</div>
  </div>
  <h1>WELCOME TO<br>KESTRELWAYMASSAGE</h1>
  <svg class="arrow" style="left:24px" width="20" height="40" viewBox="0 0 20 40"><path d="M16 4L4 20l12 16" fill="none" stroke="#fff" stroke-width="2"/></svg>
  <svg class="arrow" style="right:24px" width="20" height="40" viewBox="0 0 20 40"><path d="M4 4l12 16L4 36" fill="none" stroke="#fff" stroke-width="2"/></svg>
</section>

<section class="abs services">
  <h2>What We Do</h2><div class="rule"></div>
  <div class="service" style="left:115px"><div class="icon" role="img" aria-label="Illustration of pressed hands"></div><h3>Pain management</h3><p>Perspiciatis unde omnis iste natus error sit voluptem accusantium doloremque laudantium, totam rem aperiam, eaque ipsa quae</p></div>
  <div class="service" style="left:450px"><div class="icon" role="img" aria-label="Illustration of a therapist"></div><h3>Sports/medical</h3><p>Perspiciatis unde omnis iste natus error sit voluptem accusantium doloremque laudantium, totam rem aperiam, eaque ipsa quae</p></div>
  <div class="service" style="left:785px"><div class="icon" role="img" aria-label="Illustration of a relaxing client"></div><h3>Massage therapy</h3><p>Perspiciatis unde omnis iste natus error sit voluptem accusantium doloremque laudantium, totam rem aperiam, eaque ipsa quae</p></div>
</section>

<section class="abs band rating" role="img" aria-label="Dim spa background with massage oil bottles">
  <h2 style="padding-top:38px">5/5 Stars Massage Therapy</h2><div class="rule"></div>
  <div class="stars">
    <svg width="32" height="30" viewBox="0 0 24 23"><path fill="var(--star)" d="M12 0l3.7 7.5 8.3 1.2-6 5.8 1.4 8.3L12 18.9 4.6 22.8 6 14.5 0 8.7l8.3-1.2z"/></svg>
    <svg width="32" height="30" viewBox="0 0 24 23"><path fill="var(--star)" d="M12 0l3.7 7.5 8.3 1.2-6 5.8 1.4 8.3L12 18.9 4.6 22.8 6 14.5 0 8.7l8.3-1.2z"/></svg>
    <svg width="32" height="30" viewBox="0 0 24 23"><path fill="var(--star)" d="M12 0l3.7 7.5 8.3 1.2-6 5.8 1.4 8.3L12 18.9 4.6 22.8 6 14.5 0 8.7l8.3-1.2z"/></svg>
    <svg width="32" height="30" viewBox="0 0 24 23"><path fill="var(--star)" d="M12 0l3.7 7.5 8.3 1.2-6 5.8 1.4 8.3L12 18.9 4.6 22.8 6 14.5 0 8.7l8.3-1.2z"/></svg>
    <svg width="32" height="30" viewBox="0 0 24 23"><path fill="#fff" d="M12 0l3.7 7.5 8.3 1.2-6 5.8 1.4 8.3L12 18.9 4.6 22.8 6 14.5 0 8.7l8.3-1.2z"/></svg>
  </div>
  <p>Lina and Paul at Kestrel Way are awesome! I recently had open heart surgery, and Lina worked on me to increase my range of motion while helping with the pinched nerve from my arm being in the same position for so long during my surgery.</p>
  <div class="btn-book">BOOK NOW</div>
</section>

<section class="abs rates">
  <h2 style="padding-top:22px">Our Rates</h2><div class="rule"></div>
  <div class="card" style="left:97px"><div class="price"><b>$75</b><span>mintes</span></div><h4>60 MINUTES</h4><ul><li>Perspiciatis unde</li><li>Omnis iste natus error</li><li>Sit voluptatem mque</li></ul><div class="book">Book Now</div></div>
  <div class="card" style="left:359px"><div class="price"><b>$95</b><span>mintes</span></div><h4>90 MINUTES</h4><ul><li>Perspiciatis unde</li><li>Omnis iste natus error</li><li>Sit voluptatem mque</li></ul><div class="book">Book Now</div></div>
  <div class="card featured" style="left:619px"><div class="price"><b>$30</b><span>mintes</span></div><h4>90 MINUTES</h4><ul><li>Perspiciatis unde</li><li>Omnis iste natus error</li><li>Sit voluptatem mque</li></ul><div class="book">Book Now</div></div>
  <div class="card" style="left:877px"><div class="price"><b>$120</b><span>mintes</span></div><h4>120 MINUTES</h4><ul><li>Perspiciatis unde</li><li>Omnis iste natus error</li><li>Sit voluptatem mque</li></ul><div class="book">Book Now</div></div>
</section>

<section class="abs band clients" role="img" aria-label="Dark background of hands massaging a back">
  <h2 style="padding-top:38px">What Our Clients Say</h2><div class="rule"></div>
  <div class="client" style="left:148px"><div class="photo" role="img" aria-label="Client portrait"></div><div><div class="name">~ JOHN DOE</div><div class="role">CEO</div></div></div>
  <div class="client active" style="left:458px"><div class="photo" role="img" aria-label="Client portrait"></div><div><div class="name">~ JOHN DOE</div><div class="role">CEO</div></div></div>
  <div class="client" style="left:793px"><div class="photo" role="img" aria-label="Client portrait"></div><div><div class="name">~ JOHN DOE</div><div class="role">CEO</div></div></div>
  <svg class="abs" style="left:510px;top:256px" width="16" height="12"><path d="M0 0h16L8 12z" fill="var(--teal)"/></svg>
  <blockquote>“ Perspiciatis unde omnis iste natus error sit voluptatem accusantium loremque dantium, totam rem aperiam, eaque ipsa quae ab illo inventore veritatis et quasi architecto beatae . Nemo enim ”</blockquote>
  <svg class="arrow" style="left:34px" width="14" height="28" viewBox="0 0 14 28"><path d="M12 2L2 14l10 12" fill="none" stroke="#fff" stroke-width="2"/></svg>
  <svg class="arrow" style="right:34px" width="14" height="28" viewBox="0 0 14 28"><path d="M2 2l10 12L2 26" fill="none" stroke="#fff" stroke-width="2"/></svg>
</section>

<section class="abs passion">
  <h2 style="padding-top:28px">Our Passion</h2>
  <p class="lead">Perspiciatis unde omnis iste natus error sit voluptatem accusantium doloremque laudantium, totam rem aperiam, eaque ipsa quae ab illo inventore veritatis et quasi architecto beatae vitae dicta sunt explicabo</p>
  <div class="pitem left" style="left:20px;top:146px"><h5>Neuromuscular</h5><p>Perspiciatis unde omnis iste natus error<br>sit voluptatem accusantium dolore</p></div>
  <div class="pitem left" style="left:20px;top:264px"><h5>Myofascial release</h5><p>Perspiciatis unde omnis iste natus error<br>sit voluptatem accusantium dolore</p></div>
  <div class="pitem" style="left:860px;top:146px"><h5>Postural restoration</h5><p>Perspiciatis unde omnis iste natus error<br>sit voluptatem accusantium dolore</p></div>
  <div class="pitem" style="left:860px;top:264px"><h5>Spontaneous Muscle</h5><p>Perspiciatis unde omnis iste natus error<br>sit voluptatem accusantium dolore</p></div>
  <div class="picon" style="left:362px;top:151px" role="img" aria-label="Neuromuscular icon"></div>
  <div class="picon" style="left:362px;top:273px" role="img" aria-label="Myofascial release icon"></div>
  <div class="picon" style="left:768px;top:151px" role="img" aria-label="Postural restoration icon"></div>
  <div class="picon" style="left:768px;top:273px" role="img" aria-label="Spontaneous muscle icon"></div>
  <div class="center-logo">KESTREL<br>WAY</div>
  <svg class="abs" style="left:465px;top:170px" width="270" height="160" viewBox="0 0 270 160">
    <g fill="none" stroke="#d4d4d4" stroke-width="7" stroke-linecap="round">
      <path d="M40 32q-10-8-20-4"/><path d="M230 32q10-8 20-4"/>
      <path d="M40 128q-10 8-20 4"/><path d="M230 128q10 8 20 4"/>
    </g>
    <g fill="#d4d4d4">
      <path d="M12 22l14-2-6 14z"/><path d="M258 22l-14-2 6 14z"/>
      <path d="M12 138l14 2-6-14z"/><path d="M258 138l-14 2 6-14z"/>
    </g>
  </svg>
</section>

<footer class="abs footer">
  <nav>Home &nbsp;| &nbsp;About Us &nbsp;| &nbsp;Services &nbsp;| &nbsp;Our Passion &nbsp;| &nbsp;Testimonials &nbsp;| &nbsp;Pricing &nbsp;| &nbsp;Contacts</nav>
  <div class="copy">© 2015. kestrelwaymassage.com All rights reserved</div>
  <div class="social"><span></span><span></span><span></span><span></span><span></span></div>
</footer>

</body>
</html>
```